Small legal and financial translation company needs Squarespace website, brochure and logo

Hello,
We are Lumarin Services (www.lumarinservices-example.com), a boutique legal and financial translation company. We offer our services mainly to Spanish customers. Our primary line of business is the translation of financial statements, but we translate a wide variety legal and financial texts.
The project we are offering comprises three parts: a redo of the current website, an informational brochure for potential customer and a logo design. These three parts should provide a consistent image. We would develop content soon.
We are looking for a website that would look like a typical law firm website, nothing too fancy. Right now, it is in English, Spanish and French, although the new site need only be in English and Spanish. There must be good toggling between the English and Spanish versions. There would be no need for tie-ins to social media and it would not contain a blog. Basically, a static site. We aren't interesting in driving traffic to the site or SEO, as we will contact nearly all potential customers beforehand. The website must be built in Squarespace to enable a smooth transition. The content would be similar to the current page, we'll be working on the exact content, but a rough draft is attached.
The brochure will be some three pages and would introduce the company to potential customers, using similar images as the website and the logo to be designed.
The only specifications for the logo is, as the website and brochure, it convey a sense of security and trust.
Feel free to ask with any questions as this is the first time we have used this platform.
Thank you!
Updates

I've added a more or less final version for the text in the brochure and updated the brief. Added Wednesday, June 10, 2015

Target Market(s)

Spanish law firms, auditors, accountants, banks, investment firms

Industry/Entity Type

Finance

Logo Text

Lumarin Services

Number of Pages Required

5+ page

Font styles to use
Serif

Requirements
Must have
• The website must be built in Squarespace and have a good option to toggle between English and Spanish versions.
• Brochure must be in both English and Spanish, I'm attaching a rough draft of the information that it will probably have. This should give an idea about what to include and the spacing. I will update it to include the final information.
Nice to have
• Would be nice to have some quality finance- and legal-related images
Should not have
• Vibrant colours

```html
<!DOCTYPE html>
<html lang="en">
<head>
<meta charset="utf-8">
<title>Lumarin Services – Legal &amp; Financial Translation</title>
<link rel="stylesheet" href="https://fonts.googleapis.com/css2?family=Cinzel:wght@400;500&family=Crimson+Text:wght@400;600&family=Open+Sans:wght@300;400;600&display=swap">
<style>
:root{
  --black:#000;
  --ink:#111;
  --white:#fff;
  --paper:#f4f4f4;
  --band:#cfcfcf;
  --text:#222;
  --muted:#bbb;
  --field:#d6d6d6;
  --accent:#e03a3a;
  --link:#3b7bd8;
  --serif:'Cinzel', serif;
  --book:'Crimson Text', serif;
  --sans:'Open Sans', sans-serif;
}
*{box-sizing:border-box;margin:0;padding:0}
html,body{width:1200px;height:2226px;overflow:hidden}
body{position:relative;background:var(--white);font-family:var(--sans);color:var(--text)}
.section{position:absolute;left:0;width:1200px}

.lang-bar{top:0;height:30px;background:var(--black);color:var(--white);font-size:11px;display:flex;justify-content:flex-end;align-items:center;padding-right:82px;gap:8px}
.lang-select{border:1px solid var(--white);padding:1px 6px;font-size:10px;display:flex;gap:8px;align-items:center}

.site-header{top:30px;height:100px;border-bottom:2px solid var(--black);display:flex;align-items:center;justify-content:space-between;padding:0 96px 0 102px}
.brand{font-family:var(--serif);font-size:38px;letter-spacing:1px;color:var(--ink)}
.main-nav{display:flex;gap:38px;font-family:var(--book);font-size:19px;color:var(--ink)}

.hero{top:130px;height:696px;background:var(--band)}
.hero-photo{position:absolute;left:0;top:0;width:1200px;height:450px;background:linear-gradient(160deg,#9a9a9a 0%,#e8e8e8 35%,#bcbcbc 60%,#6f6f6f 100%)}
.hero-title{position:absolute;left:566px;top:148px;width:634px;height:87px;background:rgba(255,255,255,.55);display:flex;align-items:center;padding-left:32px;font-size:34px;font-weight:300;color:var(--ink)}
.service-card{position:absolute;top:415px;width:306px;height:230px;background:var(--black);color:var(--white);text-align:center;padding-top:78px}
.service-icon{position:absolute;left:95px;top:-58px;width:116px;height:116px;border-radius:50%;background:var(--black);border:4px solid var(--white);display:flex;align-items:center;justify-content:center}
.service-card h2{font-family:var(--serif);font-weight:400;font-size:21px;letter-spacing:1px;margin-bottom:10px}
.service-card p{font-size:15px;line-height:18px;padding:0 40px}
.btn{display:inline-block;border:1px solid var(--white);border-radius:5px;padding:3px 0;width:96px;font-size:14px;margin-top:14px}

.about{top:826px;height:426px}
.video{position:absolute;left:100px;top:55px;width:495px;height:308px;background:#222}
.video-still{position:absolute;inset:0 0 24px 0;background:linear-gradient(120deg,#8d8d8d,#d9d9d9 45%,#4d4d4d)}
.video-bar{position:absolute;left:0;bottom:0;width:100%;height:24px;background:var(--black);display:flex;align-items:center;gap:10px;padding:0 10px;color:var(--white);font-size:11px}
.progress{flex:1;height:3px;background:var(--accent)}
.about-copy{position:absolute;left:630px;top:47px;width:470px}
.about-copy h2{font-family:var(--serif);font-weight:400;font-size:29px;letter-spacing:1px;margin-bottom:14px;color:var(--ink)}
.about-copy p{font-size:15.5px;line-height:23.5px;text-align:justify}
.btn-dark{display:inline-block;border:2px solid var(--black);border-radius:6px;width:96px;text-align:center;padding:4px 0;font-size:14px;margin-top:18px}

.why{top:1252px;height:405px;background:linear-gradient(135deg,#060606,#2b2b2b 45%,#0c0c0c 70%,#262626);color:var(--white)}
.why h2{text-align:center;font-family:var(--serif);font-weight:400;font-size:28px;letter-spacing:1px;margin-top:46px}
.reason{position:absolute;top:122px;width:300px}
.reason-icon{position:absolute;left:0;top:0;width:64px;height:64px;border:2px solid var(--white);border-radius:50%;display:flex;align-items:center;justify-content:center}
.reason h3{font-family:var(--book);font-weight:400;font-size:21px;margin:13px 0 0 77px}
.reason p{margin:6px 0 0 77px;font-size:13.5px;line-height:20.5px;text-align:justify;width:214px}

.clients{top:1657px;height:281px}
.clients h2{text-align:center;font-family:var(--serif);font-weight:400;font-size:28px;letter-spacing:1px;margin-top:51px}
.client-row{position:absolute;left:100px;top:126px;width:1000px;height:102px;border:1px solid #d8d8d8;display:flex}
.client{flex:1;border-right:1px solid #d8d8d8;display:flex;align-items:center;justify-content:center;gap:8px;font-size:22px;font-weight:600;color:#333}
.client:last-child{border-right:0}
.client-dot{width:14px;height:14px;border-radius:50%;background:#333}

.site-footer{top:1938px;height:288px;background:var(--black);color:var(--white);font-size:14px}
.footer-col{position:absolute;top:42px;width:240px}
.footer-col h4{font-weight:600;font-size:16px;margin-bottom:18px}
.footer-col li{list-style:none;margin-bottom:12px;padding-left:14px;position:relative}
.footer-col li::before{content:"•";position:absolute;left:0}
.contact-line{margin-bottom:12px;line-height:22px}
.contact-line a{color:var(--link);text-decoration:none}
.field{width:230px;height:26px;background:var(--field);color:#777;font-size:11px;padding:5px 8px;margin-bottom:7px}
.field-area{height:78px}
.send{display:inline-block;border:1px solid var(--white);padding:3px 8px;font-size:12px;margin-top:6px}
</style>
</head>
<body>

<div class="section lang-bar">
  <span>Select Language:</span>
  <span class="lang-select">English <svg width="6" height="4" viewBox="0 0 6 4"><path d="M0 0h6L3 4z" fill="#fff"/></svg></span>
</div>

<header class="section site-header">
  <div class="brand">Lumarin Services</div>
  <nav class="main-nav"><span>Home</span><span>About Us</span><span>Services</span><span>FAQ's</span><span>Contact Us</span></nav>
</header>

<section class="section hero">
  <div class="hero-photo" role="img" aria-label="Black and white photo of a hand signing a document with a pen"></div>
  <div class="hero-title">HIGH-QUALITY TRANSLATION SERVICES</div>

  <div class="service-card" style="left:115px">
    <div class="service-icon">
      <svg width="56" height="56" viewBox="0 0 56 56" fill="#fff"><rect x="14" y="8" width="22" height="12" rx="2" transform="rotate(-35 25 14)"/><rect x="22" y="20" width="5" height="26" transform="rotate(-35 25 33)"/><rect x="8" y="46" width="28" height="5"/></svg>
    </div>
    <h2>Legal Translation</h2>
    <p>Lorem ipsum dolor sit amet, consectetuer adipiscing elit, sed diam nonummy nibh.</p>
    <span class="btn">More</span>
  </div>

  <div class="service-card" style="left:447px">
    <div class="service-icon">
      <svg width="50" height="50" viewBox="0 0 50 50" fill="none" stroke="#fff" stroke-width="3"><rect x="5" y="5" width="40" height="38" rx="3"/><circle cx="25" cy="24" r="9"/><path d="M10 46v2M40 46v2"/></svg>
    </div>
    <h2>Financial Translation</h2>
    <p>Lorem ipsum dolor sit amet, consectetuer adipiscing elit, sed diam nonummy nibh.</p>
    <span class="btn">More</span>
  </div>

  <div class="service-card" style="left:779px">
    <div class="service-icon">
      <svg width="60" height="40" viewBox="0 0 60 40" fill="#fff"><path d="M2 12l12-6 16 10-6 5zM58 12l-12-6-18 8 14 16 8-6z"/><path d="M18 22l10 10 4-3-10-10z"/></svg>
    </div>
    <h2>Interpreting</h2>
    <p>Lorem ipsum dolor sit amet, consectetuer adipiscing elit, sed diam nonummy nibh.</p>
    <span class="btn">More</span>
  </div>
</section>

<section class="section about">
  <div class="video">
    <div class="video-still" role="img" aria-label="Video still of a team of business professionals"></div>
    <div class="video-bar">
      <svg width="10" height="12" viewBox="0 0 10 12"><path d="M0 0l10 6-10 6z" fill="#e03a3a"/></svg>
      <span class="progress"></span>
      <span>10:00</span>
    </div>
  </div>
  <div class="about-copy">
    <h2>Who Are We?</h2>
    <p>We are a small, highly professional and qualified group of professionals with backgrounds in law, financial services and translation and interpretation that boasts experience in global consulting and auditing firms, law firms and companies from a cross section of industries. Sensitive to the workings of the financial world, we are detail-oriented experts striving to facilitate understanding among investors, companies and international organisations.</p>
    <span class="btn-dark">More</span>
  </div>
</section>

<section class="section why">
  <h2>Why Choose Us?</h2>
  <div class="reason" style="left:100px">
    <div class="reason-icon"><svg width="34" height="28" viewBox="0 0 34 28" fill="#fff"><ellipse cx="17" cy="15" rx="14" ry="10"/><rect x="8" y="22" width="5" height="6"/><rect x="21" y="22" width="5" height="6"/></svg></div>
    <h3>Save Money</h3>
    <p>Lorem ipsum dolor sit amet, consectetuer adipiscing elit, sed diam nonummy nibh euismod tincidunt ut laoreet dolore magna aliquam erat volutpat. Ut wisi enim ad minim veniam, quis nostrud exerci tation ullamcorper sudolore te feugait nulla facilisi. ..</p>
  </div>
  <div class="reason" style="left:432px">
    <div class="reason-icon"><svg width="30" height="30" viewBox="0 0 24 24" fill="#fff"><path d="M12 2l3 6.5 7 .8-5.2 4.8 1.5 7L12 17.6 5.7 21.1l1.5-7L2 9.3l7-.8z"/></svg></div>
    <h3>Quality Guaranteed</h3>
    <p>Lorem ipsum dolor sit amet, consectetuer adipiscing elit, sed diam nonummy nibh euismod tincidunt ut laoreet dolore magna aliquam erat volutpat. Ut wisi enim ad minim veniam, quis nostrud exerci tation ullamcorper sudolore te feugait nulla facilisi. ..</p>
  </div>
  <div class="reason" style="left:766px">
    <div class="reason-icon"><svg width="32" height="32" viewBox="0 0 32 32" fill="#fff"><circle cx="13" cy="13" r="6"/><path d="M2 30c0-8 5-11 11-11s11 3 11 11z"/><rect x="20" y="2" width="11" height="8" rx="3"/></svg></div>
    <h3>Native Translators Only</h3>
    <p>Lorem ipsum dolor sit amet, consectetuer adipiscing elit, sed diam nonummy nibh euismod tincidunt ut laoreet dolore magna aliquam erat volutpat. Ut wisi enim ad minim veniam, quis nostrud exerci tation ullamcorper sudolore te feugait nulla facilisi. ..</p>
  </div>
</section>

<section class="section clients">
  <h2>Our Clients</h2>
  <div class="client-row">
    <div class="client"><span class="client-dot"></span>loremipsum</div>
    <div class="client"><span class="client-dot"></span>loremipsum</div>
    <div class="client"><span class="client-dot"></span>loremipsum</div>
    <div class="client"><span class="client-dot"></span>loremipsum</div>
    <div class="client"><span class="client-dot"></span>loremipsum</div>
  </div>
</section>

<footer class="section site-footer">
  <div class="footer-col" style="left:100px">
    <h4>Quick Links</h4>
    <ul><li>Home</li><li>About Us</li><li>FAQ's</li><li>Our Clients</li><li>Privacy Policy</li></ul>
  </div>
  <div class="footer-col" style="left:351px">
    <h4>Services We Offer</h4>
    <ul><li>Legal Translation</li><li>Financial Translation</li><li>Document Translation</li><li>Interpreting</li><li>Service Levels</li></ul>
  </div>
  <div class="footer-col" style="left:601px">
    <h4>Contact Info</h4>
    <p class="contact-line">Address: 118 Harrow Bend Road<br>Fairlow, AL(Alabama) 36000</p>
    <p class="contact-line">Phone: (555) 014-2770</p>
    <p class="contact-line">Fax: &nbsp;(555) 014-2771</p>
    <p class="contact-line">Mail: <a href="#">info@lumarinservices-example.com</a></p>
  </div>
  <div class="footer-col" style="left:851px">
    <h4>Send Us a Message</h4>
    <div class="field">Name</div>
    <div class="field">Email</div>
    <div class="field field-area">Message</div>
    <span class="send">Send Message</span>
  </div>
</footer>

</body>
</html>
```